Design a Website in Wordpress for an Australian Health Training Company in Health related courses

We require a WORDPRESS based Website (due to add on's we need to use for third party software) to replace our old site.
We offer national face to face delivery in medical reception, terminology and also administration.
The website will have around 6 pages and the ability to describe our main 6 courses (perhaps on the Courses page this may be tabs opening up to details for example?)
I have attached a previous sample of a Joomla site which was being developed (please do not feel you have to copy this - but I am just giving it as a sample - copying would be boring). But it gives an idea of look/feel and colours which may be suitable. Open to other ideas though.
I will provide some of the content, but would like the ability to finish the content myself.
Images and graphics are important. While a few medical photos re great - don't be tempted to us all pictures of doctors and nurses (although a couple would be good) - these are administrative courses so general corporate, eye catching visionary pictures of people in general are great. A medical type picture is also fine.
THE BOOKING system - will be via an ADD ON which will occur at the end of the project and is supplied by a third party software company (our student management system). This project will include up to 2 hours working with the Tech guys from the third party software to enable the ADD ON. If this ADD ON requires more time, we will pay hourly (although I do not expect it will).
Target Market(s)
Mostly a female market, many mature aged women target 25-45 yrs. Mixture of medical/health and corporate. Maybe a bit of mums returning to work and corporate inspiration.
Industry/Entity Type
It Company
Coding
Coded - Design and coding required
Number of Pages Required
5+ page
Requirements
Must have
- Wordpress
- Great graphics
- Interesting
- professional and clean
- Enquiry section (info Pak)
- Should have a University feel to it - Education
- Pages
- Home Page - About Us - Recruitment -Courses - Class Schedule - Traineeships Queensland Funding - Latest News Blog - Corporate Training- Contact us

```html
<!DOCTYPE html>
<html lang="en">
<head>
<meta charset="utf-8">
<title>Harbourview Institute of Training</title>
<link rel="stylesheet" href="https://fonts.googleapis.com/css2?family=Cinzel:wght@400;700&family=Open+Sans:ital,wght@0,400;0,600;0,700;1,400&family=Raleway:wght@500;600;700&display=swap">
<style>
:root{
  --blue:#0b55b1;
  --blue-dark:#0a438f;
  --blue-deep:#083a7c;
  --navy:#0d3a7a;
  --orange:#f7931e;
  --orange-light:#fbb35e;
  --text:#666;
  --line:#dcdcdc;
  --white:#fff;
}
*{margin:0;padding:0;box-sizing:border-box}
html,body{width:1200px;height:2875px;overflow:hidden}
body{position:relative;font-family:'Open Sans',sans-serif;color:var(--text);background:var(--white)}
.band{position:absolute;left:0;width:1200px}
.abs{position:absolute}
.serif{font-family:'Cinzel',serif}

/* top bar */
.topbar{top:0;height:38px;background:var(--blue)}
.topbar .phone{left:148px;top:10px;color:var(--white);font-size:13px;font-weight:600;display:flex;align-items:center;gap:8px}
.search{left:466px;top:6px;width:172px;height:26px;display:flex}
.search input{flex:1;border:0;font-size:10px;padding:0 8px;font-family:'Open Sans',sans-serif}
.search span{width:28px;background:var(--blue-dark);display:flex;align-items:center;justify-content:center}
.social-top{right:160px;top:0;display:flex}
.social-top i{display:block;width:38px;height:38px;border-left:1px solid rgba(255,255,255,.25);position:relative}
.social-top i::after{content:"";position:absolute;left:13px;top:13px;width:12px;height:12px;background:var(--white);border-radius:2px}

/* header */
.header{top:38px;height:92px;background:var(--white)}
.logo-box{left:144px;top:38px;width:182px;height:182px;background:var(--white);box-shadow:0 2px 8px rgba(0,0,0,.25);z-index:5;text-align:center;padding-top:18px}
.logo-box .name{font-family:'Cinzel',serif;font-weight:700;color:var(--navy);font-size:17px;line-height:1.15}
.logo-box .mark{width:64px;height:64px;background:var(--navy);margin:14px auto 0}
.menu-top{top:38px;height:92px;left:370px;display:flex;align-items:center}
.menu-top a{font-family:'Raleway',sans-serif;font-size:11.5px;font-weight:600;color:#555;text-align:center;line-height:1.35;text-decoration:none}
.btn{position:absolute;left:893px;width:142px;height:30px;color:var(--white);font-family:'Raleway',sans-serif;font-size:11.5px;font-weight:700;display:flex;align-items:center;gap:10px;padding-left:10px}
.btn.enrol{top:52px;background:var(--blue)}
.btn.info{top:87px;background:#2b2b2b}
.navbar{top:130px;height:46px;background:linear-gradient(var(--orange-light),var(--orange))}
.navbar a{position:absolute;top:14px;color:var(--white);font-family:'Raleway',sans-serif;font-weight:700;font-size:14px;text-decoration:none}

/* hero */
.hero{top:176px;height:444px;background:linear-gradient(100deg,#e9ecef 0%,#f7f8f9 45%,#dfe3e8 100%)}
.hero h1{position:absolute;left:153px;top:160px;font-family:'Cinzel',serif;font-weight:700;color:var(--navy);font-size:30px;line-height:1.25}
.hero h1 span{font-size:37px}
.dots{position:absolute;display:flex;gap:6px}
.dots i{width:18px;height:18px;border-radius:50%;background:var(--white);border:2px solid #ccc}
.hero .dots{left:555px;top:409px}

/* welcome */
.welcome{top:620px;height:258px;text-align:center}
.welcome h2{margin-top:40px;font-family:'Cinzel',serif;font-weight:400;color:var(--navy);font-size:26px;line-height:1.35;letter-spacing:1px}
.welcome p{width:780px;margin:22px auto 0;font-size:12.5px;line-height:1.95;color:#777}

/* courses */
.courses{top:878px;height:334px;background:var(--blue)}
.section-title{text-align:center;font-family:'Cinzel',serif;font-size:25px;letter-spacing:1px}
.section-title::after{content:"";display:block;width:50px;height:2px;margin:10px auto 0;background:currentColor}
.courses .section-title{color:var(--white);padding-top:42px}
.course{position:absolute;display:flex;align-items:center;gap:18px;color:var(--white);font-family:'Raleway',sans-serif;font-size:15px;font-weight:500;line-height:1.5}
.course .ic{width:78px;height:78px;border:4px solid var(--white);border-radius:50%;display:flex;align-items:center;justify-content:center}

/* why */
.why{top:1212px;height:398px}
.why .section-title{color:#333;padding-top:38px;font-size:25px}
.why .section-title::after{background:var(--orange)}
.why-card{position:absolute;top:103px;width:173px;height:251px;border:1px solid var(--line);background:var(--white);text-align:center}
.why-card .ph{height:117px}
.why-card h3{font-family:'Open Sans',sans-serif;font-weight:600;color:var(--navy);font-size:15px;margin:12px 0 6px}
.why-card p{font-size:10px;line-height:1.6;color:#777;padding:0 10px;height:78px;overflow:hidden}

/* info pack */
.infopack{top:1610px;height:227px;background:linear-gradient(90deg,#4a4038 0%,#3a3a3c 40%,#2c2d30 100%)}
.infopack h2{position:absolute;left:0;width:1200px;top:22px;text-align:center;color:var(--white);font-family:'Cinzel',serif;font-weight:400;font-size:22px}
.infopack h2::after{content:"";display:block;width:50px;height:2px;margin:8px auto 0;background:var(--white)}
.field{position:absolute;width:233px;height:35px;background:var(--white);border-radius:2px;font-size:11px;color:#999;padding:10px 12px}
.submit{position:absolute;left:728px;top:132px;width:232px;height:35px;background:var(--orange);color:var(--white);font-weight:700;font-size:14px;text-align:center;line-height:35px}

/* blogs */
.blogs{top:1837px;height:425px}
.blogs .section-title{color:var(--navy);padding-top:38px}
.blog{position:absolute;top:86px;width:290px;height:285px;border:1px solid var(--line);background:var(--white)}
.blog .ph{position:absolute;left:10px;top:10px;width:268px;height:135px}
.blog .date{position:absolute;left:97px;top:125px;width:120px;height:28px;background:var(--blue);color:var(--white);font-size:11.5px;font-weight:600;text-align:center;line-height:28px}
.blog h3{position:absolute;left:20px;top:165px;color:var(--orange);font-size:15px;font-weight:600}
.blog p{position:absolute;left:20px;top:190px;width:245px;font-size:11px;line-height:1.6;color:#888}
.blog a{position:absolute;left:20px;top:254px;font-size:12px;color:#333;text-decoration:none}

/* testimonials */
.testi{top:2262px;height:291px;background:linear-gradient(90deg,var(--orange-light),#f6902a)}
.testi::before{content:"";position:absolute;left:580px;top:0;border:20px solid transparent;border-top-color:var(--white);border-bottom:0}
.testi h2{position:absolute;left:0;width:1200px;top:55px;text-align:center;color:var(--white);font-family:'Raleway',sans-serif;font-weight:600;font-size:20px}
.avatar{position:absolute;left:181px;top:114px;width:88px;height:88px;border-radius:50%;border:4px solid var(--white);background:radial-gradient(circle at 50% 40%,#d8b49a,#8a6a55)}
.testi .who{position:absolute;left:284px;top:130px;color:var(--white);font-size:15px;line-height:1.7}
.testi .who span{display:block;font-size:13px;opacity:.9}
.testi .rule{position:absolute;left:437px;top:110px;width:1px;height:100px;background:rgba(255,255,255,.6)}
.testi blockquote{position:absolute;left:470px;top:110px;width:560px;color:var(--white);font-style:italic;font-size:13.5px;line-height:2.05}
.testi blockquote b{font-size:28px;font-style:normal;line-height:0;vertical-align:-8px;margin-right:4px}
.testi .dots{left:557px;top:255px}
.testi .dots i{border:0;width:16px;height:16px}

/* footer */
.footer{top:2553px;height:265px;background:var(--blue)}
.fcol{position:absolute;top:35px;color:var(--white)}
.fcol h4{font-size:13.5px;font-weight:600;margin-bottom:16px}
.fcol .row{display:flex;gap:10px;font-size:11px;line-height:1.55;margin-bottom:12px}
.post{margin-bottom:12px}
.post strong{display:block;font-weight:400;font-size:12.5px}
.post small{display:block;font-size:10px;line-height:1.4}
.post em{display:block;font-style:normal;font-size:9.5px;margin-top:4px}
.finput{width:220px;height:32px;background:var(--white);border:1px solid #ccc;font-size:11px;color:#888;padding:9px 10px;margin-bottom:8px}
.fbtn{width:100px;height:36px;background:var(--orange);font-size:11.5px;font-weight:700;text-align:center;line-height:36px;margin-top:4px}
.soc{display:flex;align-items:center;gap:10px;font-size:12px;margin-bottom:12px}
.soc i{width:22px;height:22px;border:1.5px solid var(--white);border-radius:50%}
.bottom{top:2818px;height:57px;background:var(--blue-deep);color:#cdd8ea;font-size:10.5px;text-align:center;line-height:57px}
</style>
</head>
<body>

<div class="band topbar">
  <div class="abs phone">
    <svg width="14" height="14" viewBox="0 0 24 24"><path fill="#fff" d="M6.6 10.8a15 15 0 006.6 6.6l2.2-2.2a1 1 0 011-.25 11.4 11.4 0 003.6.57 1 1 0 011 1V20a1 1 0 01-1 1A17 17 0 013 4a1 1 0 011-1h3.5a1 1 0 011 1c0 1.25.2 2.45.57 3.6a1 1 0 01-.25 1z"/></svg>
    1800 555 0142
  </div>
  <div class="abs search"><input placeholder="Search here"><span><svg width="12" height="12" viewBox="0 0 24 24"><circle cx="10" cy="10" r="6.5" fill="none" stroke="#fff" stroke-width="3"/><path d="M15 15l6 6" stroke="#fff" stroke-width="3"/></svg></span></div>
  <div class="abs social-top"><i></i><i></i><i></i><i></i></div>
</div>

<div class="band header"></div>
<div class="abs logo-box">
  <div class="name">HARBOURVIEW<br>INSTITUTE<br>OF TRAINING</div>
  <div class="mark"></div>
</div>
<nav class="band menu-top">
  <a class="abs" style="left:20px;top:38px">ABOUT<br>US</a>
  <a class="abs" style="left:102px;top:38px">CLASS<br>SCHEDULE</a>
  <a class="abs" style="left:182px;top:38px">TRAINEESHIPS<br>QUEENSLAND FUNDING</a>
  <a class="abs" style="left:400px;top:38px">LATEST NEWS<br>BLOG</a>
</nav>
<div class="btn enrol">
  <svg width="12" height="12" viewBox="0 0 24 24"><path d="M4 4l16 8-7 2-2 7z" fill="#fff"/></svg>ENROL NOW</div>
<div class="btn info">
  <svg width="14" height="14" viewBox="0 0 24 24"><circle cx="12" cy="12" r="11" fill="#fff"/><path d="M12 10v8M12 6v1.5" stroke="#2b2b2b" stroke-width="3"/></svg>INFO PACK</div>

<nav class="band navbar">
  <a style="left:380px">HOME PAGE</a>
  <a style="left:498px">RECRUITMENT</a>
  <a style="left:636px">COURSES</a>
  <a style="left:738px">CORPORATE TRAINING</a>
  <a style="left:930px">CONTACT US</a>
</nav>

<section class="band hero" role="img" aria-label="Photo of a trainer presenting at a whiteboard to a group of office staff">
  <h1>WE PROVIDE HEALTH<br><span>EDUCATION TRAINING</span></h1>
  <div class="dots"><i></i><i></i><i></i><i></i></div>
</section>

<section class="band welcome">
  <h2>WELCOME TO<br>HARBOURVIEW INSTITUTE OF TRAINING</h2>
  <p>Harbourview is Australia's Leading Provider of Educational, Training and Support Services for the Medical and Dental industry - enabling students to be immediately skilled and 'Job Ready' for a career in Health. Harbourview is a Registered Training Organisation offering specialised Medical Administration Training in over 15 locations Australia wide. Harbourview have trained thousands of students the required knowledge and skills to become successful health care administrators</p>
</section>

<section class="band courses">
  <h2 class="section-title">OUR COURSES</h2>
  <div class="course" style="left:173px;top:105px"><span class="ic"><svg width="36" height="36" viewBox="0 0 24 24" fill="none" stroke="#fff" stroke-width="2"><path d="M9 3h6M10 3v6l-5 10a1.5 1.5 0 001.3 2h11.4a1.5 1.5 0 001.3-2l-5-10V3"/><path d="M7 15h10" /></svg></span>MEDICAL RECEPTION<br>&amp; TERMINOLOGY</div>
  <div class="course" style="left:491px;top:105px"><span class="ic"><svg width="36" height="36" viewBox="0 0 24 24" fill="none" stroke="#fff" stroke-width="2"><path d="M6 3v6a5 5 0 0010 0V3"/><path d="M11 14v2a4 4 0 008 0v-3"/><circle cx="19" cy="11" r="2"/></svg></span>MEDICAL<br>TERMINOLOGY</div>
  <div class="course" style="left:773px;top:105px"><span class="ic"><svg width="36" height="36" viewBox="0 0 24 24"><circle cx="12" cy="12" r="9" fill="#fff"/><path d="M7 8c2 0 3 2 2 4s1 3 0 5M14 5c0 2 2 2 3 4s-1 3 1 5" stroke="var(--blue)" stroke-width="1.6" fill="none"/></svg></span>HARBOURVIEW<br>ONLINE</div>
  <div class="course" style="left:173px;top:205px"><span class="ic"><svg width="36" height="36" viewBox="0 0 24 24"><rect x="3" y="7" width="18" height="13" rx="2" fill="#fff"/><path d="M9 7V5h6v2" stroke="#fff" stroke-width="2" fill="none"/><path d="M3 12h18" stroke="var(--blue)" stroke-width="1.5"/></svg></span>CERT III BUSINESS<br>ADMINISTRATION</div>
  <div class="course" style="left:491px;top:205px"><span class="ic"><svg width="38" height="38" viewBox="0 0 24 24" fill="none" stroke="#fff" stroke-width="1.8"><rect x="2" y="6" width="20" height="12" rx="2"/><path d="M5 9.5h2M9 9.5h2M13 9.5h2M17 9.5h2M5 12h2M9 12h2M13 12h2M17 12h2M7 15h10"/></svg></span>KEYBOARD AND<br>TYPING</div>
  <div class="course" style="left:773px;top:205px"><span class="ic"><svg width="36" height="36" viewBox="0 0 24 24" fill="#fff"><circle cx="7" cy="16" r="4.5"/><circle cx="17" cy="16" r="4.5"/><rect x="4" y="5" width="6" height="9" rx="1.5"/><rect x="14" y="5" width="6" height="9" rx="1.5"/><rect x="9" y="8" width="6" height="4"/></svg></span>CONFIDENTIALITY</div>
</section>

<section class="band why">
  <h2 class="section-title">WHY HARBOURVIEW INSTITUTE ?</h2>
  <div class="why-card" style="left:147px">
    <div class="ph" role="img" aria-label="Photo of a compass needle pointing to quality" style="background:linear-gradient(135deg,#1f3550,#6b86a6)"></div>
    <h3>Quality</h3><p>Harbourview delivers quality, effective training facilitated by industry leaders. Just ask our students who rate us on average of 4.7 out of 5</p></div>
  <div class="why-card" style="left:331px">
    <div class="ph" role="img" aria-label="Photo of hands joining coloured gears on a table" style="background:linear-gradient(135deg,#5a4a3e,#a58e78)"></div>
    <h3>Experience</h3><p>Harbourview is Australia's largest and leading providers of nationally recognised training in health administration – training from over 17 locations</p></div>
  <div class="why-card" style="left:515px">
    <div class="ph" role="img" aria-label="Photo of the word value made from wooden letters" style="background:linear-gradient(135deg,#c7a27c,#e3cbb0)"></div>
    <h3>Value</h3><p>Our innovative teaching approach allows us to deliver exceptional training at affordable prices with no hidden extras.</p></div>
  <div class="why-card" style="left:699px">
    <div class="ph" role="img" aria-label="Illustration of a recognition eye symbol" style="background:linear-gradient(135deg,#eef0f3,#c9d0d8)"></div>
    <h3>Industry Recognised</h3><p>Harbourview work hand in hand with industry to develop our core programme and consolidate the programme annually to keep the programme fresh and</p></div>
  <div class="why-card" style="left:881px">
    <div class="ph" role="img" aria-label="Photo of a hand-written great job note" style="background:linear-gradient(135deg,#f4f4f4,#d7dde4)"></div>
    <h3>Great Job Results</h3><p>Harbourview students get jobs! Our focus is to create job-ready students who are mentored to achieve their goals. Harbourview also provide a recruitment</p></div>
</section>

<section class="band infopack" role="img" aria-label="Photo of hands typing on a laptop on a wooden desk">
  <h2>EMAIL me an Info Pack</h2>
  <div class="field" style="left:242px;top:90px">Name</div>
  <div class="field" style="left:485px;top:90px">Email</div>
  <div class="field" style="left:728px;top:90px">Course</div>
  <div class="field" style="left:242px;top:132px">State</div>
  <div class="field" style="left:485px;top:132px">Mobile</div>
  <div class="submit">SUBMIT</div>
</section>

<section class="band blogs">
  <h2 class="section-title">LATEST BLOGS</h2>
  <article class="blog" style="left:146px">
    <div class="ph" role="img" aria-label="Photo of a smiling woman at a desk" style="background:linear-gradient(135deg,#d9c8b9,#a8bcd0)"></div>
    <div class="date">02 MAY 2016</div><h3>Aculis facilisis massa</h3>
    <p>Etiam eu urna Sed porta Suspendisse quam leo molestie sed luctus quis feugiat in pede Fusce tellus Sed metus augue</p><a>Read More</a></article>
  <article class="blog" style="left:454px">
    <div class="ph" role="img" aria-label="Photo of a classroom of students facing a teacher" style="background:linear-gradient(135deg,#8aa0bd,#d5d9de)"></div>
    <div class="date">02 MAY 2016</div><h3>Aculis facilisis massa</h3>
    <p>Etiam eu urna Sed porta Suspendisse quam leo molestie sed luctus quis feugiat in pede Fusce tellus Sed metus augue</p><a>Read More</a></article>
  <article class="blog" style="left:763px">
    <div class="ph" role="img" aria-label="Photo of students writing an exam" style="background:linear-gradient(135deg,#6f5e55,#b7a69a)"></div>
    <div class="date">02 MAY 2016</div><h3>Aculis facilisis massa</h3>
    <p>Etiam eu urna Sed porta Suspendisse quam leo molestie sed luctus quis feugiat in pede Fusce tellus Sed metus augue</p><a>Read More</a></article>
</section>

<section class="band testi">
  <h2>TESTIMONIALS</h2>
  <div class="avatar" role="img" aria-label="Portrait photo of the student"></div>
  <div class="who">Clare Bennett<span>City Location Area</span></div>
  <div class="rule"></div>
  <blockquote><b>“</b>I want to say a huge thank you for the course and knowledge I come away with. I have secured a fantastic job after my first application! Such good value for money too! I would highly recommend it. I'm a mature age person so it's never too late to up -skill yourself to get what you deserve<b>”</b></blockquote>
  <div class="dots"><i></i><i></i><i></i><i></i></div>
</section>

<footer class="band footer">
  <div class="fcol" style="left:153px">
    <h4>CONTACT US</h4>
    <div class="row"><svg width="14" height="16" viewBox="0 0 24 24"><path d="M12 2a7 7 0 00-7 7c0 5 7 13 7 13s7-8 7-13a7 7 0 00-7-7z" fill="none" stroke="#fff" stroke-width="2"/><circle cx="12" cy="9" r="2.5" fill="#fff"/></svg><span>12 Quay Lane Suite 40 Southport,<br>QLD 4215 Voice 07 5550 1282</span></div>
    <div class="row"><svg width="14" height="14" viewBox="0 0 24 24"><path fill="none" stroke="#fff" stroke-width="2" d="M6.6 10.8a15 15 0 006.6 6.6l2.2-2.2 4.6 1.3V20A17 17 0 014 4h3.5l1.3 4.6z"/></svg><span>Phone:+61 7 5550 2407</span></div>
    <div class="row"><svg width="14" height="12" viewBox="0 0 24 18"><rect x="1" y="1" width="22" height="16" fill="none" stroke="#fff" stroke-width="2"/><path d="M1 1l11 9 11-9" fill="none" stroke="#fff" stroke-width="2"/></svg><span>info@harbourview.example</span></div>
  </div>
  <div class="fcol" style="left:426px;width:220px">
    <h4>LATEST POSTS</h4>
    <div class="post"><strong>In iaculis facilisis massa Etiam</strong><small>Nam cursus Morbi ut mi Nullam enim</small><em>25 May 2016</em></div>
    <div class="post"><strong>Fusce tellus Sed</strong><small>pulvinar eu ante Integer orci tellus tristique vitae consequat nec</small><em>25 May 2016</em></div>
  </div>
  <div class="fcol" style="left:690px">
    <h4>ENQUIRY NOW</h4>
    <div style="font-size:10px;margin-bottom:12px">Excepteur sint occaecat cupidatat non proa</div>
    <div class="finput">Your Name</div>
    <div class="finput">Email address</div>
    <div class="fbtn">CLICK HERE</div>
  </div>
  <div class="fcol" style="left:972px">
    <h4>SOCIAL</h4>
    <div class="soc"><i></i>Friendbook</div>
    <div class="soc"><i></i>Chirper</div>
    <div class="soc"><i></i>Circles+</div>
    <div class="soc"><i></i>Viewtube</div>
  </div>
</footer>
<div class="band bottom">© 2016 Company Name All right reserved Term of Use</div>

</body>
</html>
```